Tolvik Commercial Cleaning is lookong for a new business card design.

A fresh new design that's professional and stylish. We need a serious upgrade to our business cards. I have included pictures of our existing ones. Our clients include professional individuals and business owners. We woupdblike something professional and upbeat. Please have fun and see what you come uo with.

Target Market(s)

Property managers, business owners, facility managers and other similar professionals

Industry/Entity Type

Janitorial

Contact Information for Business Card

Name, cell, office number, email, web address

Font styles to use
Sans Serif

Colors

Designer to choose colors to be used in the design.

Requirements
Must have
• please use the green color in our logo
Nice to have
• Bar code
Should not have
• Address

```html
<!DOCTYPE html>
<html lang="en">
<head>
<meta charset="utf-8">
<title>Tolvik Commercial Cleaning – Business Card</title>
<link href="https://fonts.googleapis.com/css2?family=Montserrat:wght@600;700&family=Open+Sans:wght@400&display=swap" rel="stylesheet">
<style>
  :root {
    --bg: #e9e8e6;
    --brand-green: #34ad50;
    --brand-green-dark: #2c9a46;
    --brand-blue: #3a6ea8;
    --card-white: #f6f6f6;
    --text-gray: #555a60;
  }
  * { margin: 0; padding: 0; box-sizing: border-box; }
  html, body {
    width: 1200px; height: 1200px; overflow: hidden;
    background: var(--bg);
  }
  .canvas { position: relative; width: 1200px; height: 1200px; }

  .card {
    position: absolute; left: 234px; width: 731px; height: 418px;
    box-shadow: 0 6px 14px rgba(0,0,0,0.12);
  }

  /* Front side */
  .card-front { top: 160px; overflow: hidden; }
  .front-pattern {
    position: absolute; inset: 0;
    background: linear-gradient(135deg, var(--brand-green-dark), var(--brand-green) 55%, #3fb55a);
  }
  .front-name {
    position: absolute; left: 0; right: 0; top: 180px;
    text-align: center;
    font-family: "Montserrat", sans-serif; font-weight: 700;
    font-size: 56px; line-height: 1; color: #ffffff;
    letter-spacing: 1px;
  }

  /* Back side */
  .card-back {
    top: 632px;
    background: linear-gradient(120deg, #fbfbfb, #ececec);
    overflow: hidden;
  }
  .company-name {
    position: absolute; left: 56px; top: 72px;
    font-family: "Montserrat", sans-serif; font-weight: 700;
    font-size: 30px; line-height: 1.15; color: var(--brand-green);
    width: 320px;
  }
  .person-name {
    position: absolute; right: 59px; top: 190px;
    font-family: "Montserrat", sans-serif; font-weight: 700;
    font-size: 30px; color: var(--brand-blue);
  }
  .contact-list {
    position: absolute; left: 56px; top: 282px;
    list-style: none;
    font-family: "Open Sans", sans-serif; font-size: 19px;
    color: var(--text-gray);
  }
  .contact-list li {
    display: flex; align-items: center; height: 28px;
  }
  .contact-list svg { width: 16px; height: 16px; margin-right: 10px; fill: var(--brand-blue); }
  .tagline {
    position: absolute; right: 59px; top: 335px;
    font-family: "Open Sans", sans-serif; font-size: 19px;
    color: var(--brand-green); letter-spacing: 0.3px;
  }
  .edge-bar { position: absolute; right: 0; width: 21px; }
  .edge-bar--top { top: 0; height: 165px; background: var(--brand-blue); border-bottom-left-radius: 8px; }
  .edge-bar--mid { top: 184px; height: 54px; background: var(--brand-green); border-radius: 8px 0 0 8px; }
  .edge-bar--bottom { top: 245px; height: 173px; background: var(--brand-blue); border-top-left-radius: 8px; }
</style>
</head>
<body>
<div class="canvas">

  <section class="card card-front">
    <div class="front-pattern" role="img" aria-label="Green background with a repeating embossed brand pattern"></div>
    <div class="front-name">Tolvik</div>
  </section>

  <section class="card card-back">
    <div class="company-name">Tolvik Commercial Cleaning</div>

    <div class="person-name">Marco Delgado</div>

    <ul class="contact-list">
      <li>
        <svg viewBox="0 0 24 24" aria-hidden="true"><path d="M6.6 10.8a15.1 15.1 0 0 0 6.6 6.6l2.2-2.2a1 1 0 0 1 1-.25 11.4 11.4 0 0 0 3.6.57 1 1 0 0 1 1 1V20a1 1 0 0 1-1 1A17 17 0 0 1 3 4a1 1 0 0 1 1-1h3.5a1 1 0 0 1 1 1c0 1.25.2 2.45.57 3.57a1 1 0 0 1-.25 1z"/></svg>
        (737) 555-0182
      </li>
      <li>
        <svg viewBox="0 0 24 24" aria-hidden="true"><path d="M2 5h20v14H2V5zm2 2v.5l8 5.5 8-5.5V7H4z"/></svg>
        marco@tolvikcleaning.com
      </li>
      <li>
        <svg viewBox="0 0 24 24" aria-hidden="true"><path d="M12 2a10 10 0 1 0 0 20 10 10 0 0 0 0-20zm6.9 9h-3a15 15 0 0 0-1.3-5.6A8 8 0 0 1 18.9 11zM12 4.1c.9 1.3 1.7 3.6 1.9 6.9h-3.8c.2-3.3 1-5.6 1.9-6.9zM9.4 5.4A15 15 0 0 0 8.1 11h-3a8 8 0 0 1 4.3-5.6zM5.1 13h3a15 15 0 0 0 1.3 5.6A8 8 0 0 1 5.1 13zM12 19.9c-.9-1.3-1.7-3.6-1.9-6.9h3.8c-.2 3.3-1 5.6-1.9 6.9zm2.6-1.3a15 15 0 0 0 1.3-5.6h3a8 8 0 0 1-4.3 5.6z"/></svg>
        www.tolvikcleaning.com
      </li>
    </ul>

    <div class="tagline">Clean Work, Done Right</div>

    <div class="edge-bar edge-bar--top"></div>
    <div class="edge-bar edge-bar--mid"></div>
    <div class="edge-bar edge-bar--bottom"></div>
  </section>

</div>
</body>
</html>
```